Retail Jewelry Business Card Design Project

We are in need of a new business card design for a retail jewelry store. This store is in the business of fine jewelry including but not specific to bridal jewelry, diamonds, designer jewelry and watches.

This store has been in business for 20 years but continues to strive for a modern professional appeal. The main colors use for this business are a royal blue, white and silver.

Target Market(s)

Target market is ages 18-50

Industry/Entity Type

Jewelry

Requirements
Must have
• Sales Person Name
Sales Person Email Address

Store Address
Store Phone
Website

Standard business card size. No odd shapes or sizes.
Nice to have
• Overall modern feel for card.

We have thought that a design with a nice feature of the logo on the back of the card would be nice but open to ideas.
Should not have
• No specific images of jewelry should be used.

```html
<!DOCTYPE html>
<html lang="en">
<head>
<meta charset="utf-8">
<title>Marlowe Reed Fine Jewelry – Business Cards</title>
<link rel="stylesheet" href="https://fonts.googleapis.com/css2?family=Jost:wght@400;500;600&display=swap">
<style>
  :root {
    --royal: #2b3990;
    --lavender: #7b77c4;
    --card: #ffffff;
    --backdrop: #ececef;
    --divider: #c9c9cf;
    --ink: #2b3990;
  }
  * { margin: 0; padding: 0; box-sizing: border-box; }
  html, body {
    width: 1200px; height: 750px; overflow: hidden;
    background: var(--backdrop);
    font-family: "Jost", sans-serif;
  }
  .sheet { position: relative; width: 1200px; height: 750px; }
  .card {
    position: absolute; top: 226px;
    width: 520px; height: 297px;
    background: var(--card);
    box-shadow: 0 2px 10px rgba(0,0,0,0.12);
    overflow: hidden;
  }
  .card--front { left: 50px; }
  .card--back { left: 630px; }

  /* wordmark */
  .wordmark { position: absolute; color: var(--royal); font-weight: 500; text-align: center; }
  .wordmark__name { display: block; line-height: 1; }
  .wordmark__line { display: block; text-transform: uppercase; }
  .card--front .wordmark { left: 40px; top: 92px; width: 230px; }
  .card--front .wordmark__name { font-size: 34px; }
  .card--front .wordmark__line { font-size: 15px; letter-spacing: 3px; margin-top: 8px; }

  .divider {
    position: absolute; left: 286px; top: 30px; width: 2px; height: 150px;
    background: linear-gradient(to bottom, rgba(201,201,207,0), var(--divider) 20%, var(--divider) 80%, rgba(201,201,207,0));
  }
  .contact { position: absolute; left: 302px; top: 34px; color: var(--ink); }
  .contact__name { font-size: 19px; font-weight: 600; margin-bottom: 18px; }
  .contact__list { list-style: none; font-size: 13px; font-weight: 400; }
  .contact__item { display: flex; align-items: center; gap: 7px; margin-bottom: 6px; }
  .contact__icon { width: 11px; height: 11px; flex: none; }

  .address-rule {
    position: absolute; left: 0; right: 0; top: 238px; height: 3px; background: var(--lavender);
  }
  .address-band {
    position: absolute; left: 0; right: 0; top: 245px; bottom: 0;
    background: var(--royal); color: #fff;
    font-size: 13px; letter-spacing: 0.3px;
    display: flex; align-items: center; padding-left: 110px;
  }

  .card--back .wordmark { left: 0; right: 0; top: 88px; }
  .card--back .wordmark__name { font-size: 50px; }
  .card--back .wordmark__line { font-size: 22px; letter-spacing: 5px; margin-top: 10px; }
  .back-web {
    position: absolute; left: 0; right: 0; top: 222px; text-align: center;
    color: var(--ink); font-size: 13px; letter-spacing: 3.5px;
  }
</style>
</head>
<body>
<main class="sheet">
  <section class="card card--front" aria-label="Business card front">
    <div class="wordmark">
      <span class="wordmark__name">Marlowe Reed</span>
      <span class="wordmark__line">Fine Jewelry</span>
    </div>
    <div class="divider"></div>
    <div class="contact">
      <p class="contact__name">Marlowe Reed Ashby</p>
      <ul class="contact__list">
        <li class="contact__item">
          <svg class="contact__icon" viewBox="0 0 12 12" aria-hidden="true"><circle cx="6" cy="6" r="5.3" fill="none" stroke="var(--royal)" stroke-width="1.2"/><path d="M4 3.2l1.2 1.4-0.6 0.8a4 4 0 0 0 2 2l0.8-0.6 1.4 1.2-0.8 1A5 5 0 0 1 3 4z" fill="var(--royal)"/></svg>
          555-201-4830
        </li>
        <li class="contact__item">
          <svg class="contact__icon" viewBox="0 0 12 12" aria-hidden="true"><rect x="1" y="2.5" width="10" height="7" rx="1" fill="var(--royal)"/><path d="M1.5 3l4.5 3.5L10.5 3" fill="none" stroke="#fff" stroke-width="1"/></svg>
          marlowe@marlowereedjewelry.com
        </li>
        <li class="contact__item">
          <svg class="contact__icon" viewBox="0 0 12 12" aria-hidden="true"><circle cx="6" cy="6" r="5" fill="var(--royal)"/><path d="M1 6h10M6 1c-2.5 3-2.5 7 0 10M6 1c2.5 3 2.5 7 0 10" fill="none" stroke="#fff" stroke-width="0.8"/></svg>
          www.marlowereedjewelry.com
        </li>
      </ul>
    </div>
    <div class="address-rule"></div>
    <p class="address-band">2280 Linden Avenue, Harbor Bay, FL 32099</p>
  </section>

  <section class="card card--back" aria-label="Business card back">
    <div class="wordmark">
      <span class="wordmark__name">Marlowe Reed</span>
      <span class="wordmark__line">Fine Jewelry</span>
    </div>
    <p class="back-web">www.marlowereedjewelry.com</p>
  </section>
</main>
</body>
</html>
```